The Founder Crossroads Book Cover

I need a Book Cover Design for a new book:
Title - "The Founder Crossroads"
Subtitle - "Lessons No Lecture Hall Ever Gave Me"
Author - "Dylan Moravec"

Target Market(s)

Entrepreneur's and Small Business Owners

Industry/Entity Type

Entrepreneur

Font styles to use
Sans Serif

Requirements
Must have
• The branding colors should match our website (Black and accent color: #FBBC05)
• http://FounderCrossroadsBook.com
• Secondary Subtile (top bar) on front of cover - "A Field Record"
• Back Cover: Brief description, author photo, and the ISBN Number
Nice to have
• A Detour Sign with the word "Detour" on it (or a sign with a "squiggly" line example) ... or a type of image that is on the bottom of Home page of website (road in wilderness).

```html
<!DOCTYPE html>
<html lang="en">
<head>
<meta charset="utf-8">
<title>The Founder Crossroads – Book Cover</title>
<link href="https://fonts.googleapis.com/css2?family=Oswald:wght@200;300;400&family=Montserrat:wght@800;900&display=swap" rel="stylesheet">
<style>
  :root {
    --stage: #969595;
    --ink: #0b0604;
    --accent: #fbbc05;
    --amber: #b57a08;
    --umber: #3a1a05;
    --paper: #ffffff;
  }
  html, body {
    margin: 0;
    padding: 0;
    width: 1200px;
    height: 1000px;
    overflow: hidden;
    background: var(--stage);
  }
  .cover {
    position: absolute;
    left: 300px;
    top: 38px;
    width: 597px;
    height: 922px;
    overflow: hidden;
    background: var(--ink);
    box-shadow: 0 2px 6px rgba(0,0,0,0.35);
  }
  .cover-photo {
    position: absolute;
    inset: 0;
    background: linear-gradient(180deg, #120804 0%, var(--umber) 22%, var(--amber) 52%, var(--umber) 74%, #100504 100%);
  }
  .cover p, .cover h1, .cover h2 { margin: 0; }
  .kicker,
  .author {
    position: absolute;
    left: 0;
    right: 0;
    text-align: center;
    font-family: "Oswald", sans-serif;
    font-weight: 300;
    color: var(--accent);
    text-transform: uppercase;
    line-height: 1;
  }
  .kicker {
    top: 30px;
    font-size: 25px;
  }
  .author {
    top: 850px;
    font-size: 34px;
  }
  .title-block {
    position: absolute;
    left: 50px;
    top: 205px;
    width: 510px;
    height: 260px;
  }
  .title-the {
    position: absolute;
    left: 0;
    top: 104px;
    transform-origin: left top;
    transform: rotate(-90deg);
    font-family: "Montserrat", sans-serif;
    font-weight: 900;
    font-size: 19px;
    letter-spacing: 1px;
    color: var(--accent);
    line-height: 1;
    text-transform: uppercase;
  }
  .title-lead {
    position: absolute;
    left: 24px;
    top: 0;
    font-family: "Oswald", sans-serif;
    font-weight: 200;
    font-size: 112px;
    line-height: 1;
    color: var(--paper);
    text-transform: uppercase;
    letter-spacing: -1px;
  }
  .title-main {
    position: absolute;
    left: 0;
    top: 114px;
    font-family: "Montserrat", sans-serif;
    font-weight: 900;
    font-size: 70px;
    line-height: 1;
    color: var(--paper);
    text-transform: uppercase;
    letter-spacing: -1.5px;
  }
  .subtitle {
    position: absolute;
    left: 0;
    top: 211px;
    font-family: "Oswald", sans-serif;
    font-weight: 300;
    font-size: 31px;
    line-height: 1;
    color: var(--paper);
    text-transform: uppercase;
  }
</style>
</head>
<body>
  <main class="cover">
    <div class="cover-photo" role="img" aria-label="Photograph: motion-blurred open highway running toward a golden sunset under amber clouds"></div>

    <p class="kicker">A Field Record</p>

    <div class="title-block">
      <span class="title-the">The</span>
      <h1 class="title-lead">Founder</h1>
      <h2 class="title-main">Crossroads</h2>
      <p class="subtitle">Lessons No Lecture Hall Ever Gave Me</p>
    </div>

    <p class="author">Dylan Moravec</p>
  </main>
</body>
</html>
```